Personal letterhead and stationary

I am looking for someone to design letterhead and stationary set for my personal use. I want something simple and timeless with a little bit of color. I like photography, computers and writing.

```html
<!DOCTYPE html>
<html lang="en">
<head>
<meta charset="utf-8">
<title>Thomas Reid Hale — Envelopes</title>
<link href="https://fonts.googleapis.com/css2?family=Josefin+Slab:wght@300;400&family=Rokkitt:wght@500&display=swap" rel="stylesheet">
<style>
  :root {
    --page: #ffffff;
    --paper: #f3e1cc;
    --ink: #2b2b2b;
    --rule: #3a3a3a;
    --seal: #1f1f1f;
    --shadow: rgba(0, 0, 0, 0.35);
  }
  html, body {
    margin: 0;
    padding: 0;
    width: 1200px;
    height: 1192px;
    overflow: hidden;
    background: var(--page);
  }
  .canvas {
    position: relative;
    width: 1200px;
    height: 1192px;
  }
  .envelope {
    position: absolute;
    left: 120px;
    width: 971px;
    height: 456px;
    background: var(--paper);
    box-shadow: 7px 7px 6px var(--shadow);
    overflow: hidden;
  }
  .envelope--back { top: 130px; }
  .envelope--front { top: 661px; }

  .envelope__svg {
    position: absolute;
    inset: 0;
  }

  .seal-name {
    position: absolute;
    font-family: "Rokkitt", Georgia, serif;
    font-weight: 500;
    color: var(--ink);
    letter-spacing: 0.08em;
    white-space: nowrap;
  }
  .envelope--back .seal-name {
    left: 556px;
    top: 108px;
    font-size: 17px;
  }
  .envelope--front .seal-name {
    left: 202px;
    top: 92px;
    font-size: 15px;
  }

  .sender {
    position: absolute;
    left: 175px;
    top: 168px;
    color: var(--ink);
  }
  .sender__name {
    margin: 0;
    font-family: "Rokkitt", Georgia, serif;
    font-weight: 500;
    font-size: 24px;
    letter-spacing: 0.06em;
    word-spacing: 0.2em;
  }
  .sender__address {
    margin: 6px 0 0;
    font-family: "Josefin Slab", Georgia, serif;
    font-weight: 400;
    font-size: 22px;
  }

  .contact {
    position: absolute;
    right: 22px;
    bottom: 10px;
    text-align: right;
    color: var(--ink);
    font-family: "Josefin Slab", Georgia, serif;
    font-weight: 300;
  }
  .contact__phone {
    margin: 0;
    font-size: 16px;
  }
  .contact__email {
    margin: 4px 0 0;
    font-size: 21px;
    font-weight: 400;
  }
</style>
</head>
<body>
<main class="canvas">

  <section class="envelope envelope--back" aria-label="Envelope back">
    <svg class="envelope__svg" width="971" height="456" viewBox="0 0 971 456">
      <line x1="0" y1="141" x2="971" y2="141" stroke="var(--rule)" stroke-width="1"/>
      <circle cx="483" cy="147" r="60" fill="var(--seal)"/>
    </svg>
    <span class="seal-name">THOMAS REID HALE</span>
  </section>

  <section class="envelope envelope--front" aria-label="Envelope front">
    <svg class="envelope__svg" width="971" height="456" viewBox="0 0 971 456">
      <line x1="132" y1="0" x2="132" y2="456" stroke="var(--rule)" stroke-width="1.2"/>
      <line x1="145" y1="0" x2="145" y2="456" stroke="var(--rule)" stroke-width="1.2"/>
      <circle cx="139" cy="104" r="52" fill="var(--seal)"/>
      <rect class="stamp-box" x="876.5" y="25.5" width="71" height="87" fill="none" stroke="var(--rule)" stroke-width="1"/>
    </svg>
    <span class="seal-name">THOMAS REID HALE</span>

    <div class="sender">
      <p class="sender__name">THOMAS REID HALE</p>
      <p class="sender__address">48 ornel st marlow vic 4512</p>
    </div>

    <div class="contact">
      <p class="contact__phone">04815523169</p>
      <p class="contact__email">Thomas@mailbox.com.au</p>
    </div>
  </section>

</main>
</body>
</html>
```